Software allocation system needs a business card design

We need a business card designed for our software platform - www.tallivo.com.au

At the moment the logo and website is all black and white, we are happy for suggestions on implementing some colour throughout either the logo or business card.

Industry/Entity Type

Software

Font styles to use
Sans Serif

Colors

Designer to choose colors to be used in the design.

```html
<!DOCTYPE html>
<html lang="en">
<head>
<meta charset="utf-8">
<title>Tallivo Business Card</title>
<link rel="stylesheet" href="https://fonts.googleapis.com/css2?family=Lato:wght@400&family=Raleway:wght@200&display=swap">
<style>
  :root {
    --stage: #131617;
    --card: #f4f6f6;
    --map-tone: #e6eaeb;
    --brand-blue: #3cb2e6;
    --text-grey: #8b9397;
    --tagline-grey: #9aa2a6;
    --icon-grey: #6f777b;
    --divider: #dfe3e4;
  }
  * { margin: 0; padding: 0; box-sizing: border-box; }
  html, body { width: 1200px; height: 720px; overflow: hidden; background: var(--stage); }
  .canvas { position: relative; width: 1200px; height: 720px; background: var(--stage); }
  .card {
    position: absolute; left: 40px; top: 40px; width: 1120px; height: 640px;
    background: var(--card); border-radius: 50px; overflow: hidden;
  }
  .world-map {
    position: absolute; left: 30px; top: 20px; width: 1060px; height: 600px;
    background: radial-gradient(ellipse at 50% 45%, var(--map-tone) 0%, rgba(230,234,235,0.5) 50%, rgba(244,246,246,0) 75%);
  }
  .brand { position: absolute; left: 13px; top: 188px; }
  .brand-name {
    display: flex; align-items: center; gap: 14px;
    font-family: "Raleway", sans-serif; font-weight: 200;
    font-size: 118px; line-height: 1; letter-spacing: 6px; color: var(--brand-blue);
  }
  .brand-dot { width: 40px; height: 40px; border-radius: 50%; background: var(--brand-blue); flex: none; }
  .tagline {
    position: absolute; left: 171px; top: 250px; white-space: nowrap;
    font-family: "Lato", sans-serif; font-size: 24px; color: var(--tagline-grey);
  }
  .divider {
    position: absolute; left: 671px; top: 133px; width: 2px; height: 360px;
    background: var(--divider); box-shadow: -6px 0 14px rgba(0,0,0,0.08);
  }
  .contact { position: absolute; left: 760px; font-family: "Lato", sans-serif; }
  .contact-title { margin-left: 40px; font-size: 22px; color: var(--brand-blue); line-height: 28px; }
  .contact-row { display: flex; align-items: center; }
  .contact-icon { width: 30px; height: 30px; margin-right: 10px; flex: none; }
  .contact-lines { font-size: 19px; line-height: 28px; color: var(--text-grey); }
  .contact-address { top: 154px; }
  .contact-phone { top: 266px; }
  .contact-web { top: 384px; }
</style>
</head>
<body>
<div class="canvas">
  <div class="card">
    <div class="world-map" role="img" aria-label="Faint dotted world map in the card background"></div>

    <div class="brand">
      <div class="brand-name"><span class="brand-dot"></span>TALLIVO</div>
    </div>
    <p class="tagline" style="top:438px;left:171px;position:absolute;">Planning &amp; Compliance for Heavy Industry</p>

    <div class="divider"></div>

    <div class="contact contact-address">
      <p class="contact-title">ADRESS</p>
      <div class="contact-row">
        <svg class="contact-icon" viewBox="0 0 30 30" aria-hidden="true">
          <path d="M3 13 L15 5 L27 13 V25 H3 Z" fill="none" stroke="var(--icon-grey)" stroke-width="2.4" stroke-linejoin="round"/>
          <path d="M3 13 L15 21 L27 13" fill="none" stroke="var(--icon-grey)" stroke-width="2.4" stroke-linejoin="round"/>
        </svg>
        <div class="contact-lines">
          <p>PO Box 218</p>
          <p>Harbour Vale NSW 2140</p>
        </div>
      </div>
    </div>

    <div class="contact contact-phone">
      <p class="contact-title">TELEPHONE &amp; FAX</p>
      <div class="contact-row">
        <svg class="contact-icon" viewBox="0 0 30 36" aria-hidden="true">
          <line x1="20" y1="1" x2="20" y2="8" stroke="var(--icon-grey)" stroke-width="2.4"/>
          <rect x="8" y="8" width="15" height="26" rx="2" fill="none" stroke="var(--icon-grey)" stroke-width="2.4"/>
          <rect x="11" y="12" width="9" height="7" fill="var(--icon-grey)"/>
          <g fill="var(--icon-grey)">
            <rect x="11" y="22" width="3" height="2"/><rect x="17" y="22" width="3" height="2"/>
            <rect x="11" y="26" width="3" height="2"/><rect x="17" y="26" width="3" height="2"/>
          </g>
        </svg>
        <div class="contact-lines">
          <p>+1 (0) 40 555 214 6830</p>
          <p>+1 (0) 40 555 367 9152</p>
        </div>
      </div>
    </div>

    <div class="contact contact-web">
      <p class="contact-title">WEB</p>
      <div class="contact-row">
        <svg class="contact-icon" viewBox="0 0 30 30" aria-hidden="true">
          <g fill="none" stroke="var(--icon-grey)" stroke-width="2">
            <circle cx="15" cy="15" r="12"/>
            <ellipse cx="15" cy="15" rx="5.5" ry="12"/>
            <line x1="3" y1="15" x2="27" y2="15"/>
            <line x1="5" y1="9" x2="25" y2="9"/>
            <line x1="5" y1="21" x2="25" y2="21"/>
          </g>
        </svg>
        <div class="contact-lines">
          <p>hello@tallivo.com.au</p>
          <p>www.tallivo.com.au</p>
        </div>
      </div>
    </div>
  </div>
</div>
</body>
</html>
```